Business Recognition Design

We need a design for a recognition to be given to business leaders in our community.
The recognition shall be made on a brass plaque on wood panel background (picture attached, please use it as a background), and all drawing must be in vectors and only one color (black).
It should also have a logo on the top and signature on the right bottom.
The text is enclosed in DOC file.
Updates

Reason: just to be able to find the best solution

Reason: None of the suggestion is good enough. Logo in general is too big in comparison with the rest of the plate.

Industry/Entity Type

Business

Requirements
Must have
• - standard Windows font (or possibility to install the same font on Windows), as the name on the recognition shall be printed in the same font
Nice to have
• - some graphic element (in curves) representing achievements in business
- should look great :)

```html
<!DOCTYPE html>
<html lang="en">
<head>
<meta charset="utf-8">
<title>Recognition Plaque</title>
<link rel="stylesheet" href="https://fonts.googleapis.com/css2?family=Jost:wght@400;500&family=Montserrat:wght@700;800&family=Open+Sans:wght@400&display=swap">
<style>
  :root {
    --wood: #c96a2c;
    --wood-dark: #a9521f;
    --frame: #6b4426;
    --frame-edge: #4e2f19;
    --brass-light: #f3dc7a;
    --brass: #e0bd3e;
    --brass-dark: #b8912a;
    --ink: #0b0b0b;
    --photo-tone: #e9cf8a;
  }
  html, body {
    margin: 0;
    padding: 0;
    width: 1200px;
    height: 930px;
    overflow: hidden;
  }
  .canvas {
    position: relative;
    width: 1200px;
    height: 930px;
    background: linear-gradient(90deg, var(--wood-dark), var(--wood) 30%, var(--wood) 70%, var(--wood-dark));
    overflow: hidden;
  }
  .wood-frame {
    position: absolute;
    left: 34px; top: 30px;
    width: 1128px; height: 870px;
    background: var(--frame);
    box-shadow: inset 0 0 0 6px var(--frame-edge), 0 6px 14px rgba(0,0,0,0.35);
  }
  .plaque {
    position: absolute;
    left: 80px; top: 76px;
    width: 1036px; height: 778px;
    background: linear-gradient(160deg, var(--brass-dark) 0%, var(--brass) 25%, var(--brass-light) 55%, var(--brass) 80%, var(--brass-dark) 100%);
    overflow: hidden;
    color: var(--ink);
  }
  .plaque-wave {
    position: absolute;
    left: 0; top: 0;
    width: 1036px; height: 778px;
  }
  .screw {
    position: absolute;
    width: 28px; height: 28px;
    border-radius: 50%;
    background: radial-gradient(circle at 40% 35%, #fff4b8, #d9b43c 50%, #7a5a14 100%);
    box-shadow: 0 1px 2px rgba(0,0,0,0.5);
  }
  .screw.tl { left: 26px; top: 20px; }
  .screw.tr { left: 994px; top: 20px; }
  .screw.bl { left: 28px; top: 726px; }
  .screw.br { left: 996px; top: 726px; }
  .logo-text {
    position: absolute;
    left: 68px; top: 86px;
    margin: 0;
    font-family: "Montserrat", sans-serif;
    font-weight: 800;
    font-size: 78px;
    line-height: 1;
  }
  .title {
    position: absolute;
    left: 68px; top: 244px;
    margin: 0;
    font-family: "Montserrat", sans-serif;
    font-weight: 800;
    font-size: 44px;
    letter-spacing: 5px;
    line-height: 1;
  }
  .award {
    position: absolute;
    left: 68px; top: 338px;
    margin: 0;
    font-family: "Jost", sans-serif;
    font-size: 35px;
    line-height: 1;
  }
  .recipient {
    position: absolute;
    left: 70px; top: 393px;
    margin: 0;
    font-family: "Jost", sans-serif;
    font-size: 28px;
    line-height: 1;
  }
  .recipient-name {
    font-family: "Montserrat", sans-serif;
    font-weight: 700;
    font-size: 25px;
  }
  .citation {
    position: absolute;
    left: 62px; top: 466px;
    margin: 0;
    font-family: "Jost", sans-serif;
    font-size: 30px;
    line-height: 46px;
  }
  .company { font-weight: 500; }
  .date {
    position: absolute;
    left: 72px; top: 632px;
    margin: 0;
    font-family: "Open Sans", sans-serif;
    font-size: 22px;
  }
  .date sup { font-size: 11px; }
  .signatory {
    position: absolute;
    left: 764px; top: 622px;
    margin: 0;
    font-family: "Open Sans", sans-serif;
    font-size: 27px;
  }
  .photo-slot {
    position: absolute;
    left: 692px; top: 72px;
    width: 292px; height: 360px;
    background: radial-gradient(ellipse at 50% 50%, var(--photo-tone), rgba(233,207,138,0) 75%);
  }
</style>
</head>
<body>
<div class="canvas">
  <div class="wood-frame"></div>
  <div class="plaque">
    <svg class="plaque-wave" viewBox="0 0 1036 778" aria-hidden="true">
      <path d="M0,660 C180,716 300,770 440,766 C640,758 820,680 1036,676 L1036,778 L0,778 Z" fill="#0b0b0b"/>
      <path d="M40,668 C200,730 320,758 460,750 C660,740 840,678 1000,676" fill="none" stroke="#6a6a6a" stroke-width="10" stroke-linecap="round"/>
      <path d="M40,662 C210,740 320,778 480,772 C680,762 860,690 1036,684" fill="none" stroke="#d4ae3a" stroke-width="3"/>
    </svg>
    <div class="screw tl"></div>
    <div class="screw tr"></div>
    <div class="screw bl"></div>
    <div class="screw br"></div>

    <p class="logo-text">(Your Logo)</p>
    <h1 class="title">RECOGNITION</h1>
    <p class="award">The Best Entrepreneur in 2013</p>
    <p class="recipient">to&nbsp; Mr. <span class="recipient-name">Daniel R. Whitfield,</span> MBA</p>
    <p class="citation">Under the leadership of Mr. Daniel R. Whitfield, MBA<br>
      the company <span class="company">DR-WHITFIELD Ltd</span> has been selected<br>
      by a City Council as the best company of The City.</p>
    <p class="date">Date: 4<sup>th</sup>July, 2013</p>
    <p class="signatory">City Mayor</p>

    <div class="photo-slot" role="img" aria-label="Photo of several raised hands giving thumbs up"></div>
  </div>
</div>
</body>
</html>
```